Business Card Design - Property Management & Real Estate Services

I need a business card design for my company that I can print ZEPLA Cards. The company is called Brindle Management Company. It is a property management and real estate company. The design has to be clean and modern. I need two versions. One for my employee and one for me. However, the design will be the same, just different text. You can get a feel for the company by looking at our website at www.brindlemanagement.example.

Industry/Entity Type

Property Management

Contact Information for Business Card

I will be using ZEPLA.com to print my cards. I will most likely use the rounded edges card. I need two versions, however, they will be the same design. I need one for me and my employee.

Colors
3276b5
33a6d7

Requirements
Must have
• Company Logo
• Name of person
• Property Management & Real Estate Service
• Phone
• Email
• Website
• Address
• A space to place a QR code

```html
<!DOCTYPE html>
<html lang="en">
<head>
<meta charset="UTF-8">
<title>Brindle Management – Business Cards</title>
<link href="https://fonts.googleapis.com/css2?family=Roboto:wght@400;500&family=Roboto+Condensed:wght@400;700&display=swap" rel="stylesheet">
<style>
  :root {
    --bg: #c9c9c9;
    --card: #fbfbfb;
    --navy: #1b4f9c;
    --blue: #3276b5;
    --light-blue: #6a9bd4;
    --text: #2d2d2d;
    --muted: #555;
    --white: #ffffff;
  }
  * { margin: 0; padding: 0; box-sizing: border-box; }
  html, body {
    width: 1200px; height: 852px; overflow: hidden;
    background: var(--bg);
    font-family: "Roboto", Arial, sans-serif;
  }
  .stage { position: relative; width: 1200px; height: 852px; }
  .card {
    position: absolute;
    width: 520px; height: 297px;
    background: var(--card);
    border-radius: 18px;
    overflow: hidden;
    box-shadow: 0 3px 8px rgba(0,0,0,.18);
  }
  .card--front { left: 60px; top: 278px; }
  .card--back { left: 620px; top: 278px; }
  .card__band { position: absolute; left: 0; bottom: 0; width: 520px; }

  .brand-name {
    color: var(--navy);
    font-family: "Roboto", Arial, sans-serif;
    font-weight: 500;
    letter-spacing: 1px;
    text-transform: uppercase;
    line-height: 1.1;
    text-align: center;
  }
  .card--front .brand-name {
    position: absolute; left: 0; right: 0; top: 100px;
    font-size: 34px;
  }
  .front__web {
    position: absolute; left: 0; right: 0; top: 200px;
    text-align: center; font-size: 14px; color: var(--text);
  }
  .front__rule {
    position: absolute; top: 232px; left: 160px; width: 200px;
    height: 1px; background: var(--blue);
  }

  .card--back .brand-name {
    position: absolute; left: 30px; top: 110px; width: 210px;
    font-size: 25px;
  }
  .person { position: absolute; left: 262px; top: 42px; }
  .person__name {
    font-family: "Roboto Condensed", Arial, sans-serif;
    font-weight: 700; font-size: 20px; color: var(--navy);
  }
  .person__role { font-size: 13px; color: var(--muted); margin-top: 2px; }
  .contact { list-style: none; margin-top: 14px; }
  .contact li {
    display: flex; align-items: center; gap: 7px;
    font-size: 12.5px; color: var(--text); line-height: 19px;
  }
  .contact svg { width: 11px; height: 11px; flex: none; fill: var(--navy); }
  .contact .no-icon { padding-left: 18px; }
  .tagline {
    position: absolute; right: 14px; bottom: 14px;
    font-family: "Roboto Condensed", Arial, sans-serif;
    font-size: 13px; color: var(--white);
  }
</style>
</head>
<body>
<main class="stage">

  <section class="card card--front" aria-label="Card front">
    <div class="brand-name">Brindle Management</div>
    <div class="front__web">www.brindlemanagement.example</div>
    <div class="front__rule"></div>
    <svg class="card__band" height="14" viewBox="0 0 520 14" aria-hidden="true">
      <rect x="0" y="0" width="520" height="14" fill="var(--light-blue)"/>
      <polygon points="270,0 520,0 520,14 262,14" fill="var(--navy)"/>
    </svg>
  </section>

  <section class="card card--back" aria-label="Card back">
    <div class="brand-name">Brindle Management</div>
    <div class="person">
      <div class="person__name">Tomas R. Ibarra</div>
      <div class="person__role">Founder</div>
      <ul class="contact">
        <li>
          <svg viewBox="0 0 12 12"><path d="M2 1h2l1 3-1.5 1a6 6 0 0 0 3.5 3.5L8 7l3 1v2a1 1 0 0 1-1 1A9 9 0 0 1 1 2a1 1 0 0 1 1-1z"/></svg>
          (305) 555-0148
        </li>
        <li>
          <svg viewBox="0 0 12 12"><path d="M0 2h12v8H0z M0 2l6 4 6-4" stroke="var(--card)" stroke-width="1"/></svg>
          tomas@brindlemanagement.example
        </li>
        <li>
          <svg viewBox="0 0 12 12"><circle cx="6" cy="6" r="5.5"/></svg>
          www.brindlemanagement.example
        </li>
        <li class="no-icon">480 Harbor Ave #210 Miami, FL 33130</li>
      </ul>
    </div>
    <svg class="card__band" height="60" viewBox="0 0 520 60" aria-hidden="true">
      <rect x="0" y="48" width="520" height="12" fill="var(--light-blue)"/>
      <path d="M230 60 L236 16 Q238 6 250 6 L520 6 L520 60 Z" fill="var(--navy)"/>
    </svg>
    <div class="tagline">Miami Property Management &amp; Real Estate Services</div>
  </section>

</main>
</body>
</html>
```